VOR Exterior Coatings

double sided. the front i want the name of the business each word on a new line with the VOR being bigger. id like teal, black and white colors. the back i want my contact info. Flat, no gloss. Something professional and I want to feel the letters bump put of the card. if possible maybe a paint sprayer in corner. not a car paint spray. (no tank on top of gun)
no vehicle paint sprayers. that means no tank on top of the gun. doesn't have to have a sprayer. black/dark background on the front. white back ground on back with info

```html
<!DOCTYPE html>
<html lang="en">
<head>
<meta charset="utf-8">
<title>VOR Exterior Coatings – Business Cards</title>
<link rel="stylesheet" href="https://fonts.googleapis.com/css2?family=Michroma&family=Roboto:wght@400;500&display=swap">
<style>
  :root {
    --backdrop: #e0e0e0;
    --paper: #ffffff;
    --charcoal: #262828;
    --teal: #0e8a87;
    --teal-deep: #064a52;
    --ink: #1e1e1e;
    --light-text: #e2e2e2;
    --shadow: rgba(0, 0, 0, 0.55);
  }
  * { box-sizing: border-box; margin: 0; padding: 0; }
  html, body {
    width: 1200px;
    height: 801px;
    overflow: hidden;
    background: var(--backdrop);
  }
  .stage {
    position: relative;
    width: 1200px;
    height: 801px;
  }
  .card {
    position: absolute;
    top: 274px;
    width: 443px;
    height: 263px;
    box-shadow: 2px 2px 0 var(--shadow);
    overflow: hidden;
  }
  .card--front { left: 153px; background: var(--paper); }
  .card--back  { left: 625px; background: var(--charcoal); }

  .wordmark {
    position: absolute;
    font-family: "Michroma", sans-serif;
    font-weight: 400;
    line-height: 1;
    text-transform: uppercase;
  }
  .wordmark span { display: block; white-space: nowrap; }
  .wordmark__lead { font-size: 54px; letter-spacing: 2px; }
  .wordmark__line { font-size: 19.5px; letter-spacing: -0.3px; margin-top: 4px; }

  .card--front .wordmark { left: 22px; top: 26px; color: var(--ink); }
  .card--back .wordmark {
    left: 0; right: 0; top: 42px;
    text-align: center;
    color: var(--light-text);
  }
  .card--back .wordmark__lead { font-size: 62px; }
  .card--back .wordmark__line { font-size: 24px; margin-top: 5px; }

  .person {
    position: absolute;
    left: 29px;
    top: 152px;
  }
  .person__name {
    font-family: "Michroma", sans-serif;
    font-size: 13px;
    color: var(--teal);
    letter-spacing: 0;
    line-height: 1.2;
    text-transform: uppercase;
  }
  .person__role {
    font-family: "Roboto", sans-serif;
    font-size: 13px;
    color: var(--ink);
    margin-top: 2px;
  }

  .contact {
    position: absolute;
    left: 28px;
    top: 192px;
    list-style: none;
    font-family: "Roboto", sans-serif;
    font-size: 12.6px;
    color: var(--ink);
  }
  .contact li {
    display: flex;
    align-items: center;
    height: 16.5px;
  }
  .contact svg { width: 13px; height: 13px; margin-right: 5px; flex: none; }
  .contact .accent { color: var(--teal); }

  .spray-photo {
    position: absolute;
    left: 205px;
    top: 86px;
    width: 238px;
    height: 177px;
    background:
      linear-gradient(100deg, rgba(235, 40, 40, 0.55) 0%, rgba(235, 40, 40, 0) 22%),
      radial-gradient(ellipse at 60% 60%, #6d7178 0%, #b9bec6 45%, rgba(255,255,255,0) 80%),
      linear-gradient(160deg, #ffffff 0%, #eef1f6 40%, #cfd8e8 100%);
  }

  .address-band {
    position: absolute;
    left: 0;
    right: 0;
    top: 192px;
    height: 32px;
    background: var(--teal-deep);
    display: flex;
    align-items: center;
    justify-content: center;
    font-family: "Roboto", sans-serif;
    font-size: 13px;
    color: #ffffff;
  }
</style>
</head>
<body>
<main class="stage">

  <section class="card card--front" aria-label="Business card front">
    <div class="wordmark">
      <span class="wordmark__lead">VOR</span>
      <span class="wordmark__line">Exterior</span>
      <span class="wordmark__line">Coatings</span>
    </div>

    <div class="person">
      <p class="person__name">Daniel Reyes</p>
      <p class="person__role">Managing Director</p>
    </div>

    <ul class="contact">
      <li>
        <svg viewBox="0 0 24 24" aria-hidden="true"><path fill="none" stroke="#0e8a87" stroke-width="2.2" d="M6 3l3 5-2 2c1 3 4 6 7 7l2-2 5 3-2 3C11 21 3 13 3 5z"/></svg>
        044-987 654 321
      </li>
      <li>
        <svg viewBox="0 0 24 24" aria-hidden="true"><rect x="2" y="5" width="20" height="14" fill="#0e8a87"/><path d="M2 5l10 8 10-8" fill="none" stroke="#ffffff" stroke-width="1.6"/></svg>
        info@vorcoatings.com
      </li>
      <li>
        <svg viewBox="0 0 24 24" aria-hidden="true"><g fill="none" stroke="#0e8a87" stroke-width="1.8"><circle cx="12" cy="12" r="10"/><ellipse cx="12" cy="12" rx="4.5" ry="10"/><path d="M2 12h20M4 7h16M4 17h16"/></g></svg>
        <span>www.<span class="accent">vorcoatings</span>.com</span>
      </li>
    </ul>

    <div class="spray-photo" role="img" aria-label="Photo of an electric paint sprayer with hose and blue motor unit spraying red paint"></div>
  </section>

  <section class="card card--back" aria-label="Business card back">
    <div class="wordmark">
      <span class="wordmark__lead">VOR</span>
      <span class="wordmark__line">Exterior</span>
      <span class="wordmark__line">Coatings</span>
    </div>
    <div class="address-band">87 Harbor Road, Jacksonville, 32202</div>
  </section>

</main>
</body>
</html>
```